Design and Renovation Company Luxury Business Card

I want to create a luxury business card for a Design and Renovation Firm . We will use our current logo. The company name is 528BUILDA. We do not want anything standard. We need a very unique concept.
Please see uploaded inspiration. I really like the textured paper option. I would like the card to be thick with debossing, and/or embossing options. The logo has orange in it but I would like to see the card with and without the orange. I think the orange may make the company feel less high-end. The goal is to elevate the logo not match its vibe per se of the logo. We want something very unique, not standard at all!
I would like a space for :
Logo,
Name,
Position,
Email,
Office number,
Website Address,
Business Address,
Thank you!
Have fun!
Target Market(s)
Home owners Age 35 +
Industry/Entity Type
Design and Renovation
Contact Information for Business Card
Logo, Name, Position, Email, Office number, Website Address, Business Address,.
Colors
Designer to choose colors to be used in the design.
Requirements
Must have
- A luxury designer feel. Must be black or dark grey but open to other luxury ideas.
Nice to have
- Gold, silver, black embossing or debossing. Textured paper design.
Should not have
- A cheap look and feel.

```html
<!DOCTYPE html>
<html lang="en">
<head>
<meta charset="utf-8">
<title>528BUILDA Business Card</title>
<link rel="stylesheet" href="https://fonts.googleapis.com/css2?family=Poppins:wght@300;400;500;600&display=swap">
<style>
  :root {
    --backdrop: #d3d7d7;
    --card: #232427;
    --card-deep: #1b1c1f;
    --card-mid: #1f2023;
    --ink: #ffffff;
    --tile-light: #d9d9d9;
    --tile-mid: #5a5b5e;
    --tile-dark: #141517;
  }
  * { margin: 0; padding: 0; box-sizing: border-box; }
  html, body {
    width: 1200px; height: 960px; overflow: hidden;
    background: var(--backdrop);
    font-family: "Poppins", sans-serif;
    color: var(--ink);
  }
  .canvas { position: relative; width: 1200px; height: 960px; }
  .card {
    position: absolute; top: 105px; width: 429px; height: 750px;
    box-shadow: 0 10px 28px rgba(0,0,0,0.35);
    overflow: hidden;
  }
  .card-back { left: 142px; }
  .tile-field {
    width: 100%; height: 100%;
    background:
      linear-gradient(160deg, var(--tile-light) 0%, #9c9d9f 14%, var(--tile-mid) 30%, #2c2d30 48%, var(--tile-dark) 100%);
  }
  .card-front { left: 631px; background: var(--card); text-align: center; }
  .waves { position: absolute; left: 0; top: 0; width: 429px; height: 750px; }
  .brand { position: absolute; top: 52px; left: 0; right: 0; }
  .brand-square { width: 74px; height: 74px; background: var(--ink); margin: 0 auto; }
  .brand-name {
    margin-top: 48px; font-size: 27px; font-weight: 500; letter-spacing: 2.5px; line-height: 1;
  }
  .person { position: absolute; top: 306px; left: 0; right: 0; }
  .person-name { font-size: 33px; line-height: 1.1; font-weight: 300; letter-spacing: 0.3px; }
  .person-name strong { font-weight: 600; }
  .person-role { font-size: 16.5px; font-weight: 500; margin-top: 1px; letter-spacing: 0.3px; }
  .icon-row {
    position: absolute; top: 386px; left: 0; right: 0;
    display: flex; justify-content: center; gap: 7px;
  }
  .icon { width: 27px; height: 27px; border-radius: 50%; background: var(--ink); display: flex; align-items: center; justify-content: center; }
  .icon svg { width: 16px; height: 16px; }
  .contact { position: absolute; top: 427px; left: 0; right: 0; font-size: 18px; line-height: 25px; font-weight: 400; letter-spacing: 0.3px; }
  .address-icon { position: absolute; top: 633px; left: 201px; }
  .address { position: absolute; top: 662px; left: 0; right: 0; font-size: 17.5px; line-height: 25px; letter-spacing: 0.3px; }
</style>
</head>
<body>
<main class="canvas">
  <section class="card card-back">
    <div class="tile-field" role="img" aria-label="Metallic mosaic tile pattern fading from silver at the top to black"></div>
  </section>

  <section class="card card-front">
    <svg class="waves" viewBox="0 0 429 750" aria-hidden="true">
      <defs>
        <linearGradient id="shadeA" x1="0" y1="0" x2="0" y2="1">
          <stop offset="0" stop-color="#18191b"/>
          <stop offset="1" stop-color="#1e1f22"/>
        </linearGradient>
      </defs>
      <path d="M0 479 Q214 620 429 472 L429 750 L0 750 Z" fill="url(#shadeA)"/>
      <path d="M0 486 Q180 610 429 608 L429 750 L0 750 Z" fill="var(--card-mid)"/>
      <path d="M0 634 Q170 610 215 593 Q320 610 429 608 L429 750 L0 750 Z" fill="var(--card)"/>
    </svg>

    <div class="brand">
      <div class="brand-square"></div>
      <div class="brand-name">528BUILDA</div>
    </div>

    <div class="person">
      <h1 class="person-name"><strong>Marta</strong> Velinova</h1>
      <p class="person-role">Founder &amp; CEO</p>
    </div>

    <div class="icon-row">
      <span class="icon"><svg viewBox="0 0 24 24" fill="none" stroke="#232427" stroke-width="2" stroke-linecap="round"><path d="M5 3h4l2 5-2.5 1.5a11 11 0 0 0 6 6L16 13l5 2v4a2 2 0 0 1-2 2A16 16 0 0 1 3 5a2 2 0 0 1 2-2z"/></svg></span>
      <span class="icon"><svg viewBox="0 0 24 24" fill="none" stroke="#232427" stroke-width="2" stroke-linejoin="round"><rect x="3" y="6" width="18" height="13"/><path d="M3 6l9 7 9-7"/></svg></span>
      <span class="icon"><svg viewBox="0 0 24 24" fill="none" stroke="#232427" stroke-width="2"><circle cx="12" cy="12" r="9"/><path d="M3 12h18M12 3c3 3 3 15 0 18M12 3c-3 3-3 15 0 18"/></svg></span>
    </div>

    <div class="contact">
      <p>(555) 204-8816</p>
      <p>info@528builda.com</p>
      <p>www.528builda.com</p>
    </div>

    <span class="icon address-icon"><svg viewBox="0 0 24 24" fill="none" stroke="#232427" stroke-width="2"><path d="M12 21s-6-6-6-11a6 6 0 0 1 12 0c0 5-6 11-6 11z"/><circle cx="12" cy="10" r="2"/></svg></span>
    <div class="address">
      <p>1840 Linden Ave. Suite 300</p>
      <p>Cedar Falls, TX 75011</p>
    </div>
  </section>
</main>
</body>
</html>
```